Millcrest PTA Website Design

We are working with Millcrest Elementary School PTA. They are a Parent Teacher Association that needs a new website design.

A Parent Teacher Association (PTA) is a volunteer organization that brings parents, teachers, and school staff together to support students and enhance their educational experience. PTAs organize fundraisers, sponsor school events, advocate for education policies, and foster stronger connections between families and schools.

Some sites to use for inspiration:

https://parentboardhub.com/demo/
https://nonprofits.kindlyfundr.com/blogs/more-great-pta-websites-you-should-copy
https://www.rvmxpta.com

Thank you for taking the time to consider designing a website for us. We are web developers based in Stockton and Los Angeles, CA, USA. Most of our projects go through the same process. Understanding this process may help you win a project with us. We custom-code all of our websites in-house. We don’t have any requirements as to what tools you use for your design, but we prefer Figma files. For any design that we label as four-stars, we send it to the client for review. The client picks the final design they want us to use. Once we complete this process, we will continue to show additional clients all the four-star sites and purchase them later. Your designs will have multiple chances to sell. For better chances of success, we ask that you follow these guidelines.

IMAGES:
If you use any images or icons in the design, we ask that you have a link to the asset so we can purchase the image/icon. Most of the designs we submit do not have the customer’s images on them unless they have some great images. Be creative; show us the feeling you are trying to portray with your image choices. Use any royalty-free site you choose. We subscribe to Adobe and mainly use their images, but we can purchase images outside of Adobe.

PLEASE NOTE: we will not submit designs to clients with watermarks on the images.

FONTS:
We ask that you identify the fonts used in the design. This can be done in a message if you want. We typically use Google Fonts and Adobe Fonts.

CONTENT:
We're always open to different content and ideas. We often submit designs with stock images so the client can see our vision. We typically take pictures after the website launch to use their images with our vision. Lorem Ipsum is fine for paragraphs, but we ask that you write the headers in correct English. We want to be able to show the vision and identify the sections of the website.

INSPIRATION:
We typically add a couple of links in the brief of websites we like to help you get started in your design.

REVISIONS:
We do not often ask for revisions of the designs unless we see something in the design that may not appeal to the client. If there are slight changes that we want to make, we do that in the development process.

FEEDBACK:
We rarely give feedback on designs during the design process. We are working on many website projects and do not have the time to provide feedback. We usually respond if your request is well thought out and asks specific questions, but a note asking “feedback, please” usually goes unanswered.

```html
<!DOCTYPE html>
<html lang="en">
<head>
<meta charset="utf-8">
<title>Millcrest PTA</title>
<link rel="stylesheet" href="https://fonts.googleapis.com/css2?family=Poppins:ital,wght@0,400;0,500;0,600;0,700;0,800;1,500&display=swap">
<style>
:root{
  --navy:#1e2f6f;
  --orange:#f7a600;
  --ink:#2b2b2b;
  --white:#ffffff;
  --footer:#141414;
  --line:#b9bccb;
}
*{box-sizing:border-box;margin:0;padding:0}
html,body{width:1200px;height:4402px;overflow:hidden}
body{font-family:"Poppins",sans-serif;color:var(--ink);background:var(--white);position:relative}
.abs{position:absolute}
a{color:inherit;text-decoration:none}
.btn{position:absolute;background:var(--orange);color:var(--white);border-radius:24px;font-size:16px;font-weight:500;display:flex;align-items:center;justify-content:center}
.media{position:absolute}
.title{position:absolute;font-size:26px;font-weight:400;color:var(--navy);letter-spacing:.3px;white-space:nowrap}
.body-text{position:absolute;font-size:14px;line-height:26.5px;color:var(--ink)}
.band{position:absolute;left:0;width:1200px;background:var(--navy)}

/* header */
.brand-mark{left:73px;top:14px;width:58px;height:75px;background:var(--navy)}
.brand-name{left:148px;top:20px;font-size:27px;font-weight:700;color:var(--navy);letter-spacing:.5px}
.brand-tag{left:148px;top:56px;font-size:18px;font-weight:500;color:var(--ink)}
.social-btn{left:844px;top:24px;width:282px;height:53px;border:1.5px solid #9a9a9a;border-radius:27px;display:flex;align-items:center;justify-content:center;font-size:15px;font-weight:600;color:var(--ink)}
.main-nav{left:0;top:99px;width:1200px;height:55px;background:var(--navy)}
.nav-item{position:absolute;top:19px;font-size:12px;font-weight:700;color:var(--white);text-transform:uppercase;letter-spacing:.2px}
.nav-item.active{color:var(--orange)}

/* hero */
.hero{left:0;top:154px;width:1200px;height:567px;
  background:
    radial-gradient(ellipse 260px 200px at 180px 120px,rgba(214,170,120,.9),transparent),
    radial-gradient(ellipse 300px 180px at 420px 460px,rgba(200,60,70,.55),transparent),
    radial-gradient(ellipse 260px 160px at 760px 420px,rgba(70,150,200,.5),transparent),
    radial-gradient(ellipse 280px 200px at 1000px 300px,rgba(230,120,60,.5),transparent),
    radial-gradient(ellipse 300px 160px at 620px 520px,rgba(80,160,90,.45),transparent),
    linear-gradient(180deg,#6e5644 0%,#b08a66 45%,#9a7a5c 75%,#5c4a3d 100%)}
.hero-shade{left:0;top:154px;width:1200px;height:567px;background:rgba(0,0,0,.22)}
.hero-title{left:0;top:345px;width:1200px;text-align:center;color:var(--white);font-size:37px;font-weight:800;letter-spacing:.3px}
.hero-sub{left:0;top:393px;width:1200px;text-align:center;color:var(--white);font-size:23px;font-weight:500;line-height:31px}
.dot{position:absolute;top:672px;width:11px;height:11px;border-radius:50%;background:var(--white)}
.dot.current{background:#333}

/* contact */
.contact-head{position:absolute;font-size:26px;font-weight:400;color:var(--navy)}
.icon-circle{position:absolute;left:73px;width:42px;height:42px;border-radius:50%;background:var(--navy);display:flex;align-items:center;justify-content:center}
.contact-line{position:absolute;left:128px;font-size:15px;color:var(--ink)}
.field{position:absolute;border:1.5px solid var(--line);border-radius:25px;font-size:14.5px;color:#444;padding-left:22px;display:flex;align-items:center}
.field.area{align-items:flex-start;padding-top:18px;border-radius:22px}

/* footer */
.site-footer{left:0;top:4259px;width:1200px;height:143px;background:var(--footer)}
.foot-item{position:absolute;top:4304px;font-size:12px;font-weight:700;color:var(--white);text-transform:uppercase}
.copyright{left:0;top:4338px;width:1200px;text-align:center;font-size:13px;color:var(--white)}
</style>
</head>
<body>

<header>
  <div class="abs brand-mark"></div>
  <div class="abs brand-name">MILLCREST PTA</div>
  <div class="abs brand-tag">BACK WITH A ROAR!</div>
  <a class="abs social-btn" href="#">MILLCREST PTA ON SOCIAL</a>
  <nav class="abs main-nav">
    <a class="nav-item active" style="left:87px">Home</a>
    <a class="nav-item" style="left:159px">PTA &amp; You!</a>
    <a class="nav-item" style="left:268px">Millcrest PTA Store</a>
    <a class="nav-item" style="left:453px">PTA-Funded Progams</a>
    <a class="nav-item" style="left:644px">Blue &amp; White</a>
    <a class="nav-item" style="left:767px">Millcrest Elementary Website</a>
    <a class="nav-item" style="left:1027px">Contact Us</a>
  </nav>
</header>

<section>
  <div class="media hero" role="img" aria-label="Photo of children doing colourful paper crafts at a classroom table"></div>
  <div class="abs hero-shade"></div>
  <h1 class="abs hero-title">TOGETHER, WE MAKE MILLCREST STRONGER</h1>
  <p class="abs hero-sub">Building a better school community through connection,<br>volunteerism, and support.</p>
  <a class="btn" style="left:511px;top:477px;width:176px;height:43px">Donate Today</a>
  <span class="dot" style="left:564px"></span>
  <span class="dot current" style="left:585px"></span>
  <span class="dot" style="left:605px"></span>
  <span class="dot" style="left:626px"></span>
</section>

<section>
  <div class="media" style="left:73px;top:783px;width:513px;height:258px;background:
    radial-gradient(ellipse 120px 80px at 210px 60px,rgba(30,47,111,.8),transparent),
    radial-gradient(ellipse 260px 90px at 250px 220px,rgba(190,120,90,.65),transparent),
    radial-gradient(ellipse 120px 70px at 420px 200px,rgba(90,160,150,.55),transparent),
    linear-gradient(180deg,#e9ecef 0%,#dfe2e6 45%,#c8b6a3 100%)" role="img" aria-label="Photo of smiling students in art aprons in a classroom"></div>
  <div class="media" style="left:614px;top:783px;width:512px;height:258px;background:
    linear-gradient(180deg,transparent 32%,rgba(230,210,200,.55) 40%,rgba(200,120,140,.45) 55%,rgba(90,140,200,.45) 62%,transparent 72%),
    radial-gradient(circle at 30% 30%,#c79463,#a8743f 60%,#8d5f34)" role="img" aria-label="Corkboard with pinned paper letters spelling volunteer"></div>
  <h2 class="title" style="left:73px;top:1064px">PTA Membership and Meetings</h2>
  <p class="body-text" style="left:73px;top:1107px;width:480px">Interested in joining?&nbsp; Joining Millcrest PTA online is as simple as a 1-2-3…or A-B-C! Join us here!!</p>
  <a class="btn" style="left:73px;top:1186px;width:153px;height:45px">Learn More</a>
  <h2 class="title" style="left:614px;top:1064px">Volunteer with PTA!</h2>
  <p class="body-text" style="left:614px;top:1107px;width:480px">Become a PTA volunteer today! Join the Board… Plan an activity or event… Help in the classroom…</p>
  <a class="btn" style="left:614px;top:1186px;width:153px;height:45px">Learn More</a>
</section>

<section>
  <div class="band" style="top:1309px;height:371px"></div>
  <div class="media" style="left:0;top:1309px;width:586px;height:371px;background:
    radial-gradient(ellipse 200px 130px at 200px 150px,rgba(160,205,235,.95),transparent),
    radial-gradient(ellipse 160px 90px at 420px 320px,rgba(220,190,170,.8),transparent),
    linear-gradient(135deg,#d4d7db 0%,#9aa5b1 50%,#4d5058 100%)" role="img" aria-label="Laptop on a desk showing a donate page with a heart"></div>
  <h2 class="title" style="left:615px;top:1352px;color:var(--white)">Give Back!</h2>
  <p class="body-text" style="left:615px;top:1396px;width:500px;color:var(--white)">PTA works hard to provide an incredible array of programs and experiences for all our Millcrest Lions!&nbsp; With an operating budget of approximately $50,000 per year, your support is pivotal to ensuring all our Lions can&nbsp; experience field trips, monthly art lessons, STEM experiments, assemblies, drama program opportunities and more.</p>
  <a class="btn" style="left:615px;top:1581px;width:152px;height:44px">Donate Now</a>
</section>

<section>
  <h2 class="title" style="left:73px;top:1847px">2024 Fall Carnival</h2>
  <p class="body-text" style="left:73px;top:1890px;width:650px">Join the fun and support the Millcrest 6th Graders! Carnival games, tasty food, yummy treats and loads of fun are just a few weeks away! Bonus: Wear your favorite non-gruesome, non-scary costume and get 2 extra carnival tickets.</p>
  <p class="body-text" style="left:73px;top:1989px;color:var(--navy);font-style:italic;font-weight:500;font-size:15px">Don't miss out! Pre-purchase Dinner and Carnival Tickets TODAY!</p>
  <a class="btn" style="left:73px;top:2037px;width:153px;height:45px">Learn More</a>
  <div class="media" style="left:766px;top:1753px;width:333px;height:433px;background:
    radial-gradient(ellipse 150px 70px at 166px 60px,rgba(190,50,50,.75),transparent),
    radial-gradient(ellipse 130px 40px at 166px 130px,rgba(40,130,120,.7),transparent),
    radial-gradient(circle at 50% 48%,#fbeab0 0%,#f5c976 45%,#eba257 75%,#d9793f 100%)" role="img" aria-label="Fall costume carnival event poster, October 25, 2024, 5:30pm to 8pm"></div>
</section>

<section>
  <div class="band" style="top:2263px;height:371px"></div>
  <div class="media" style="left:0;top:2263px;width:586px;height:371px;background:
    radial-gradient(ellipse 180px 120px at 100px 80px,rgba(220,60,80,.6),transparent),
    radial-gradient(ellipse 150px 100px at 280px 140px,rgba(50,110,200,.6),transparent),
    radial-gradient(ellipse 160px 100px at 420px 300px,rgba(40,150,80,.55),transparent),
    radial-gradient(ellipse 140px 90px at 520px 120px,rgba(240,210,70,.6),transparent),
    linear-gradient(135deg,#d8a65a,#c48a44 50%,#a86e36)" role="img" aria-label="Colourful school supplies scattered on a wooden desk"></div>
  <h2 class="title" style="left:615px;top:2316px;color:var(--white)">Millcrest Yearbook</h2>
  <p class="body-text" style="left:615px;top:2359px;width:470px;color:var(--white)">Parents, students, family and friends!&nbsp; Break out that camera and snap those pics!&nbsp; 1st day of school, Red Ribbon Week, Spirit days - whatever the event, we want your photos!</p>
  <p class="body-text" style="left:615px;top:2446px;width:530px;color:var(--white)">Send your pics to <span style="color:var(--orange);text-decoration:underline">millcrestlionsyearbook@examplemail.com</span> to have your students' photos featured in this year's yearbook.</p>
  <a class="btn" style="left:615px;top:2524px;width:152px;height:45px">Learn More</a>
</section>

<section>
  <div class="media" style="left:73px;top:2711px;width:513px;height:258px;background:
    linear-gradient(180deg,#dfe5f2 0%,#dfe5f2 26%,transparent 26%),
    radial-gradient(ellipse 160px 120px at 420px 150px,rgba(30,47,111,.85),transparent),
    linear-gradient(180deg,#f4f5f9,#e3e7f0 70%,#c9d1e4)" role="img" aria-label="Blue and White dinner and auction save-the-date flyer, Saturday April 27"></div>
  <div class="media" style="left:614px;top:2711px;width:512px;height:258px;background:
    radial-gradient(ellipse 110px 120px at 120px 150px,rgba(200,120,110,.55),transparent),
    radial-gradient(ellipse 110px 120px at 260px 160px,rgba(110,80,70,.55),transparent),
    radial-gradient(ellipse 110px 120px at 400px 150px,rgba(220,170,120,.55),transparent),
    linear-gradient(180deg,#7f9c55 0%,#a7bb72 45%,#6b5a48 100%)" role="img" aria-label="Photo of children sharing a picnic lunch on a park bench"></div>
  <h2 class="title" style="left:73px;top:2992px">2024 Blue and white dinner and auction</h2>
  <p class="body-text" style="left:73px;top:3035px;width:490px">Join us on Saturday, April 27 2024 for the best night of the year! Millcrest PTA is hosting our adults-only biennial dinner and auction supporting the Millcrest Arts program at Maple Terrace starting at 5:30.</p>
  <a class="btn" style="left:73px;top:3162px;width:153px;height:44px">Learn More</a>
  <h2 class="title" style="left:614px;top:2992px">Spring Picnic</h2>
  <p class="body-text" style="left:614px;top:3035px;width:500px">Friday, May 3 is our annual Spring Picnic supporting the next 6th grade class!&nbsp; Join us for a fantastic Starship-themed evening of food, friends, and lots of fun!</p>
  <a class="btn" style="left:614px;top:3162px;width:153px;height:44px">Learn More</a>
</section>

<section>
  <div class="band" style="top:3280px;height:371px"></div>
  <h2 class="title" style="left:0;top:3372px;width:1200px;text-align:center;color:var(--white);font-size:26px">Important Dates</h2>
  <p class="body-text" style="left:0;top:3414px;width:1200px;text-align:center;color:var(--white);line-height:32px">Don't miss out on important PTA events throughout the year!&nbsp; Stay tuned for important 2022-2023 dates!<br>Also, keep up with minimum days, vacation days and district-wide events by getting the Riverbend Unified Schools calendar here.</p>
  <a class="btn" style="left:525px;top:3504px;width:152px;height:44px">Learn More</a>
</section>

<section>
  <h2 class="contact-head" style="left:73px;top:3708px">Contact Info</h2>
  <div class="icon-circle" style="top:3763px"><svg width="18" height="16" viewBox="0 0 18 16"><path d="M1 3l5-2 6 2 5-2v12l-5 2-6-2-5 2z" fill="#fff"/></svg></div>
  <p class="contact-line" style="top:3773px">1480 Orchard Lane Fairhaven, CA 95012</p>
  <div class="icon-circle" style="top:3816px"><svg width="16" height="16" viewBox="0 0 16 16"><path d="M3 1l3 3-2 2c1 2 3 4 5 5l2-2 3 3-2 3C6 14 2 10 1 3z" fill="#fff"/></svg></div>
  <p class="contact-line" style="top:3826px">(555)301-4827</p>
  <div class="icon-circle" style="top:3869px"><svg width="18" height="13" viewBox="0 0 18 13"><rect x="0" y="0" width="18" height="13" rx="1.5" fill="#fff"/><path d="M1 1l8 6 8-6" fill="none" stroke="#1e2f6f" stroke-width="1.6"/></svg></div>
  <p class="contact-line" style="top:3879px">ptamillcrestlions@examplemail.com</p>
  <div class="media" style="left:73px;top:3948px;width:513px;height:234px;border:1px solid #d0d0d0;background:
    radial-gradient(ellipse 120px 60px at 100px 130px,rgba(170,215,165,.8),transparent),
    radial-gradient(ellipse 140px 60px at 380px 200px,rgba(175,220,170,.8),transparent),
    radial-gradient(ellipse 160px 50px at 300px 60px,rgba(200,220,240,.7),transparent),
    linear-gradient(135deg,#eef1f2,#e6ebe8 50%,#e9eef2)" role="img" aria-label="Street map showing the school location"></div>

  <h2 class="contact-head" style="left:615px;top:3708px">Good to know</h2>
  <div class="field" style="left:615px;top:3774px;width:248px;height:49px">First Name</div>
  <div class="field" style="left:877px;top:3774px;width:249px;height:49px">Last Name</div>
  <div class="field" style="left:615px;top:3840px;width:511px;height:48px">Email Address</div>
  <div class="field area" style="left:615px;top:3909px;width:511px;height:205px">Message</div>
  <a class="btn" style="left:615px;top:4133px;width:248px;height:48px">Submit Now</a>
</section>

<footer>
  <div class="abs site-footer"></div>
  <a class="foot-item" style="left:87px">Home</a>
  <a class="foot-item" style="left:159px">PTA &amp; You!</a>
  <a class="foot-item" style="left:268px">Millcrest PTA Store</a>
  <a class="foot-item" style="left:453px">PTA-Funded Progams</a>
  <a class="foot-item" style="left:644px">Blue &amp; White</a>
  <a class="foot-item" style="left:767px">Millcrest Elementary Website</a>
  <a class="foot-item" style="left:1027px">Contact Us</a>
  <p class="abs copyright">Copyright © 2025 Millcrest PTA. All Right Reserved</p>
</footer>

</body>
</html>
```